Ravnaas-Lilleby Group AS

We need a design for our company including background pictures on our web (wix-template), redesign of logo and reports. Our company delivers personality test and services to clients when hiring staff or related to organizatonal developement.

Target Market(s)

Unisex, Age 30-50, managers in private corporations

Industry/Entity Type

Recruitment

Logo Text

Bygger laget sterkt (english translate: buids your team strong)

Number of Pages Required

1 page

Font styles to use
Sans Serif

Colors
add136
34a6d7
0255a3

Requirements
Must have
• The ideal designer will be the one to bring my narrative come to life. And it will have to include the testresults report and redesign (!) of my logo. Following the attached brief in ppt:
• - the testresult report
• - redesign logo
• - graphic elements in a maritime narrative
• - including the boat, the radar, 7 GULLs, the compass etc
Nice to have
• A strong narrative with a lot of elements.
• I really like the green color in the attached breif ;-)

```html
<!DOCTYPE html>
<html lang="no">
<head>
<meta charset="utf-8">
<title>Analyse Rapport</title>
<link rel="stylesheet" href="https://fonts.googleapis.com/css2?family=Montserrat:wght@700;800;900&family=Roboto:wght@400;700&display=swap">
<style>
  :root {
    --green: #5e7d34;
    --blue: #3fb0e5;
    --ink: #2c2c2c;
    --dots: #97b08a;
    --box-line: #8a8a8a;
    --white: #ffffff;
    --sky-light: #ffffff;
    --sky-deep: #b5d9ee;
    --icon-tint: #cfe8f6;
  }
  * { margin: 0; padding: 0; box-sizing: border-box; }
  html, body { width: 1001px; height: 1200px; overflow: hidden; }
  body { font-family: "Roboto", Arial, sans-serif; color: var(--ink); background: var(--white); }

  .report {
    position: relative; width: 1001px; height: 1200px; overflow: hidden;
    background: radial-gradient(ellipse 75% 60% at 50% 45%, var(--sky-light) 35%, var(--sky-deep) 100%);
  }

  .report-header {
    position: absolute; left: 0; top: 0; width: 100%; height: 122px;
    background: var(--white);
  }
  .report-title {
    position: absolute; left: 45px; top: 27px;
    font-family: "Montserrat", Arial, sans-serif; font-weight: 900;
    font-size: 60px; letter-spacing: 0.5px; color: var(--green); line-height: 1;
  }
  .brand-name {
    position: absolute; right: 38px; top: 44px; width: 130px; text-align: right;
    font-family: "Montserrat", Arial, sans-serif; font-weight: 800;
    font-size: 15px; line-height: 1.2; color: var(--green);
  }
  .scallop { position: absolute; left: 0; top: 116px; }

  .grid-lines { position: absolute; left: 0; top: 0; pointer-events: none; }

  .trait { position: absolute; width: 500px; text-align: center; }
  .trait-icon {
    width: 116px; height: 104px; margin: 0 auto; border-radius: 14px;
    background: var(--icon-tint);
  }
  .trait-name {
    font-family: "Montserrat", Arial, sans-serif; font-weight: 800;
    font-size: 30px; color: var(--blue); letter-spacing: 0.5px; line-height: 1; margin-top: 6px;
  }
  .trait-arrow { display: block; margin: 0 auto; }
  .trait-text {
    text-align: left; font-size: 14.4px; line-height: 19.5px; color: var(--ink);
    margin-top: 6px;
  }

  .meter { position: absolute; text-align: center; }
  .meter-label {
    font-family: "Montserrat", Arial, sans-serif; font-weight: 800;
    font-size: 32px; color: var(--green); letter-spacing: 0.3px; line-height: 1;
  }

  .scale { position: absolute; width: 444px; }
  .scale-bar {
    height: 46px; background: var(--blue); color: var(--white);
    font-family: "Montserrat", Arial, sans-serif; font-weight: 800; font-size: 28px;
    display: flex; align-items: center; justify-content: center; letter-spacing: 1px;
  }
  .scale-row { position: absolute; left: 10px; width: 432px; height: 40px; }
  .scale-row span {
    position: absolute; left: 0; top: 11px;
    font-family: "Montserrat", Arial, sans-serif; font-weight: 700; font-size: 18px; color: var(--ink);
  }
  .scale-row i {
    position: absolute; right: 0; top: 0; width: 210px; height: 40px;
    border: 1.5px solid var(--box-line); background: transparent;
  }
</style>
</head>
<body>
<main class="report">
  <header class="report-header">
    <h1 class="report-title">ANALYSE RAPPORT</h1>
    <div class="brand-name">Nordvik Analyse AS</div>
  </header>
  <svg class="scallop" width="1001" height="16" viewBox="0 0 1001 16" aria-hidden="true">
    <defs>
      <pattern id="wave" width="20" height="16" patternUnits="userSpaceOnUse">
        <path d="M0 6 Q5 14 10 6 Q15 14 20 6" fill="none" stroke="var(--green)" stroke-width="2.5"/>
      </pattern>
    </defs>
    <rect width="1001" height="16" fill="url(#wave)"/>
  </svg>

  <svg class="grid-lines" width="1001" height="1200" aria-hidden="true">
    <g stroke="var(--dots)" stroke-width="3" stroke-dasharray="0 8" stroke-linecap="round" fill="none">
      <line x1="497" y1="136" x2="497" y2="750"/>
      <line x1="0" y1="437" x2="1001" y2="437"/>
      <line x1="0" y1="757" x2="1001" y2="757"/>
      <line x1="0" y1="928" x2="1001" y2="928"/>
      <line x1="497" y1="936" x2="497" y2="1200" opacity="0.5"/>
    </g>
  </svg>

  <section class="trait" style="left:0; top:157px;">
    <div class="trait-icon" role="img" aria-label="Ikon: arbeider med spade"></div>
    <h2 class="trait-name">WORKER</h2>
    <svg class="trait-arrow" width="182" height="10" aria-hidden="true"><line x1="0" y1="5" x2="174" y2="5" stroke="var(--blue)" stroke-width="2"/><path d="M172 0 L182 5 L172 10Z" fill="var(--blue)"/></svg>
    <p class="trait-text" style="margin-left:127px;">Worker er effektiv og bekymret for<br>ting som kan forsinke produksjonen.<br>Kan være for kritisk i andres øyne.<br>Faresignal: "martyrkultur".</p>
  </section>

  <section class="trait" style="left:517px; top:157px;">
    <div class="trait-icon" role="img" aria-label="Ikon: puslespillbrikker"></div>
    <h2 class="trait-name">INTEGRATOR</h2>
    <svg class="trait-arrow" width="262" height="10" aria-hidden="true"><line x1="0" y1="5" x2="254" y2="5" stroke="var(--blue)" stroke-width="2"/><path d="M252 0 L262 5 L252 10Z" fill="var(--blue)"/></svg>
    <p class="trait-text" style="margin-left:109px;">Integrator er opptatt av menneskene<br>og involverer mange i å løse oppgaven.<br>Kan være for avhengig av andres støtte.<br>Faresignal: ”kappevender”.</p>
  </section>

  <section class="trait" style="left:0; top:481px;">
    <div class="trait-icon" role="img" aria-label="Ikon: kompass"></div>
    <h2 class="trait-name">NAVIGATOR</h2>
    <svg class="trait-arrow" width="244" height="10" aria-hidden="true"><line x1="0" y1="5" x2="236" y2="5" stroke="var(--blue)" stroke-width="2"/><path d="M234 0 L244 5 L234 10Z" fill="var(--blue)"/></svg>
    <p class="trait-text" style="margin-left:124px;">Navigator peker retning. Han tror alt er<br>mulig og kan være for bred i sin<br>tilnærming – overser (viktige) detaljer.<br>Faresignal: "Brannstifter".</p>
  </section>

  <section class="trait" style="left:517px; top:481px;">
    <div class="trait-icon" role="img" aria-label="Ikon: utklippstavle med penn"></div>
    <h2 class="trait-name">DICIPLINE</h2>
    <svg class="trait-arrow" width="196" height="10" aria-hidden="true"><line x1="0" y1="5" x2="188" y2="5" stroke="var(--blue)" stroke-width="2"/><path d="M186 0 L196 5 L186 10Z" fill="var(--blue)"/></svg>
    <p class="trait-text" style="margin-left:109px;">Diciplin er forutsigbar og overholder<br>sine ansvarsområder. Kan være for<br>avhengig av stabilitet. Faresignal:<br>"byråkratisk kultur".</p>
  </section>

  <div class="meter" style="left:140px; top:789px; width:142px;">
    <svg width="120" height="50" viewBox="0 0 120 50" aria-hidden="true">
      <rect x="3" y="3" width="100" height="44" rx="8" fill="none" stroke="var(--green)" stroke-width="6"/>
      <rect x="105" y="14" width="10" height="22" rx="2" fill="none" stroke="var(--green)" stroke-width="5"/>
      <path d="M14 13 H72 L84 37 H14 Z" fill="var(--green)"/>
    </svg>
    <div class="meter-label" style="margin-top:28px;">ENERGI</div>
  </div>

  <div class="meter" style="left:594px; top:789px; width:332px;">
    <svg width="120" height="50" viewBox="0 0 120 50" aria-hidden="true">
      <rect x="3" y="3" width="100" height="44" rx="8" fill="none" stroke="var(--green)" stroke-width="6"/>
      <rect x="105" y="14" width="10" height="22" rx="2" fill="none" stroke="var(--green)" stroke-width="5"/>
      <path d="M14 13 H30 L42 37 H14 Z" fill="var(--green)"/>
    </svg>
    <div class="meter-label" style="margin-top:28px;">PROBLEMLØSNING</div>
  </div>

  <section class="scale" style="left:24px; top:952px; height:180px;">
    <div class="scale-bar">LYTTE</div>
    <div class="scale-row" style="top:77px;"><span>EMPATI</span><i></i></div>
    <div class="scale-row" style="top:130px;"><span>SELVDISIPLIN</span><i></i></div>
  </section>

  <section class="scale" style="left:531px; top:952px; height:130px;">
    <div class="scale-bar">SENDE</div>
    <div class="scale-row" style="top:77px; left:3px; width:440px;"><span>MARKERINGSEVNE</span><i style="width:202px;"></i></div>
  </section>
</main>
</body>
</html>
```